Business Card Design

My business is writing crime novels to entertain readers. I write legal thrillers and mysteries. I need a card for publishers, agents, other authors, and media.

Industry/Entity Type

Legal

Contact Information for Business Card

Paul Derrow
www.derrowfiction.example
pauljderrow@inkpost.example
0064 27 5190472

```html
<!DOCTYPE html>
<html lang="en">
<head>
<meta charset="utf-8">
<title>Paul Derrow – Business Card</title>
<link href="https://fonts.googleapis.com/css2?family=Arimo:wght@400&display=swap" rel="stylesheet">
<style>
  :root {
    --page-bg: #ededed;
    --card-grey: #7c7c7c;
    --slate-dark: #4b5966;
    --slate-mid: #71808b;
    --slate-light: #b4bec5;
    --sheen: #ffffff;
    --name-ink: #3b4855;
    --text-white: #ffffff;
    --text-pale: #dbe2e8;
    --portrait-top: #9a9a9a;
    --portrait-bottom: #2b2b2b;
  }
  * { box-sizing: border-box; margin: 0; padding: 0; }
  html, body {
    width: 848px;
    height: 1200px;
    overflow: hidden;
    background: var(--page-bg);
  }
  .canvas {
    position: relative;
    width: 848px;
    height: 1200px;
  }
  .business-card {
    position: absolute;
    left: 44px;
    top: 388px;
    width: 760px;
    height: 423px;
    overflow: hidden;
    box-shadow: 0 2px 10px rgba(0,0,0,0.18);
    font-family: "Arimo", Arial, sans-serif;
  }
  .card-shapes {
    position: absolute;
    inset: 0;
    width: 100%;
    height: 100%;
    display: block;
  }
  .identity {
    position: absolute;
    left: 84px;
    top: 132px;
  }
  .identity .name {
    color: var(--name-ink);
    font-size: 25px;
    line-height: 1;
    letter-spacing: 0.2px;
  }
  .identity .role {
    color: var(--text-white);
    font-size: 18px;
    line-height: 1;
    margin-top: 8px;
  }
  .contact {
    position: absolute;
    left: 84px;
    top: 238px;
    list-style: none;
  }
  .contact .phone {
    color: var(--text-white);
    font-size: 23px;
    line-height: 1;
    margin-bottom: 9px;
  }
  .contact .email,
  .contact .web {
    color: var(--text-pale);
    font-size: 20px;
    line-height: 1;
    margin-bottom: 9px;
  }
</style>
</head>
<body>
<main class="canvas">
  <section class="business-card" aria-label="Business card for Paul Derrow">
    <svg class="card-shapes" viewBox="0 0 527 293" preserveAspectRatio="none" xmlns="http://www.w3.org/2000/svg">
      <defs>
        <linearGradient id="slateBand" x1="0" y1="0" x2="1" y2="0">
          <stop offset="0" stop-color="var(--slate-mid)"/>
          <stop offset="1" stop-color="var(--slate-dark)"/>
        </linearGradient>
        <linearGradient id="topSheen" x1="0" y1="0" x2="1" y2="0">
          <stop offset="0" stop-color="var(--sheen)"/>
          <stop offset="0.55" stop-color="#e6eaec"/>
          <stop offset="1" stop-color="#8d99a2"/>
        </linearGradient>
        <linearGradient id="bottomBand" x1="0" y1="0" x2="1" y2="0">
          <stop offset="0" stop-color="var(--slate-dark)"/>
          <stop offset="0.6" stop-color="var(--slate-mid)"/>
          <stop offset="1" stop-color="var(--slate-light)"/>
        </linearGradient>
        <linearGradient id="bottomSheen" x1="0" y1="0" x2="1" y2="0">
          <stop offset="0" stop-color="#aab4bb"/>
          <stop offset="1" stop-color="#eef1f3"/>
        </linearGradient>
        <linearGradient id="portraitTone" x1="0" y1="0" x2="0" y2="1">
          <stop offset="0" stop-color="var(--portrait-top)"/>
          <stop offset="0.45" stop-color="#6e6e6e"/>
          <stop offset="1" stop-color="var(--portrait-bottom)"/>
        </linearGradient>
      </defs>

      <rect class="card-base" width="527" height="293" fill="var(--card-grey)"/>

      <path class="top-band" d="M0,0 H527 V42 C400,34 210,56 0,82 Z" fill="url(#slateBand)"/>
      <path class="top-sheen" d="M0,0 H527 V12 C390,14 170,30 0,64 Z" fill="url(#topSheen)"/>
      <path class="top-streak" d="M60,70 C160,52 260,40 360,34" fill="none" stroke="#ffffff" stroke-opacity="0.7" stroke-width="1.2"/>

      <path class="bottom-band" d="M0,246 C140,272 300,268 527,238 V293 H0 Z" fill="url(#bottomBand)"/>
      <path class="bottom-sheen" d="M0,282 C160,290 320,284 527,262 V293 H0 Z" fill="url(#bottomSheen)"/>

      <rect class="portrait" x="343" y="28" width="184" height="265" fill="url(#portraitTone)" role="img" aria-label="Portrait photo of the author in glasses, white shirt and dark leather jacket"/>
    </svg>

    <header class="identity">
      <h1 class="name">Paul Derrow</h1>
      <p class="role">Writer</p>
    </header>

    <ul class="contact">
      <li class="phone">0064 27 5190472</li>
      <li class="email">pauljderrow@inkpost.example</li>
      <li class="web">www.derrowfiction.example</li>
    </ul>
  </section>
</main>
</body>
</html>
```